Landscape design build company door flyer

I would like this flyer to convey a high-level of professionalism for a company that is excellent with communication with their clients as well as a company that does incredible installations

Went on vacation/holiday

```html
<!DOCTYPE html>
<html lang="en">
<head>
<meta charset="UTF-8">
<title>Cedar Ridge Builders – Door Flyer</title>
<link href="https://fonts.googleapis.com/css2?family=Montserrat:wght@500;600;700;800&family=Poppins:wght@500;600;700&family=Roboto+Condensed:wght@700&display=swap" rel="stylesheet">
<style>
  :root {
    --orange: #ef7a1a;
    --navy: #15324a;
    --ink: #1d1d1d;
    --paper: #f1f1f1;
    --panel: #e6e6e6;
    --stage: #e8e8e8;
    --white: #ffffff;
  }
  * { margin: 0; padding: 0; box-sizing: border-box; }
  html, body { width: 1200px; height: 1029px; overflow: hidden; background: var(--stage); }
  body { position: relative; font-family: "Montserrat", sans-serif; color: var(--ink); }

  .flyer {
    position: absolute; left: 112px; top: 47px;
    width: 726px; height: 934px;
    background: var(--paper); overflow: hidden;
    border: 1px solid #cfcfcf;
  }

  .hero-photo {
    position: absolute; left: 0; top: 0; width: 726px; height: 508px;
    background:
      linear-gradient(180deg, rgba(0,0,0,0) 70%, #4f8a3a 100%),
      linear-gradient(100deg, #8fa3a8 0%, #7f9598 40%, #6d7e74 62%, #2f5234 80%, #1f3d25 100%);
  }

  .brand-panel { position: absolute; left: 0; top: 0; width: 380px; height: 158px; }
  .brand-panel svg { position: absolute; inset: 0; }
  .brand {
    position: absolute; left: 0; width: 316px; top: 52px; text-align: center;
  }
  .brand-mark {
    width: 40px; height: 40px; border-radius: 50%;
    background: var(--orange); margin: 0 auto 10px;
  }
  .brand-name {
    font-family: "Montserrat", sans-serif; font-weight: 700;
    font-size: 17px; letter-spacing: 0.5px; color: var(--orange); line-height: 1;
  }
  .brand-tagline {
    margin-top: 4px; font-size: 8.5px; font-weight: 500;
    color: var(--navy); letter-spacing: 0.3px;
  }

  .gallery-photo {
    position: absolute; top: 391px; width: 192px; height: 192px;
    border-radius: 50%; border: 6px solid var(--white);
  }
  .gallery-photo.deck { left: 43px; background: linear-gradient(160deg, #5d8a4a 0%, #8a4a2a 55%, #a5532c 100%); }
  .gallery-photo.pavilion { left: 268px; background: linear-gradient(170deg, #7a9a6a 0%, #b27a44 40%, #6d7378 75%, #5b8e3c 100%); }
  .gallery-photo.steps { left: 492px; background: linear-gradient(180deg, #55683a 0%, #7a5a3e 25%, #5c6166 45%, #3e4246 100%); }

  .section-title {
    position: absolute; top: 622px;
    font-family: "Poppins", sans-serif; font-weight: 600;
    font-size: 22px; line-height: 1; color: var(--navy);
  }
  .section-title .accent { color: var(--orange); }
  .about-title { left: 32px; }
  .services-title { left: 429px; }

  .about-column {
    position: absolute; left: 32px; top: 664px; width: 308px;
    display: flex; flex-direction: column; gap: 15px;
  }
  .about-text {
    font-size: 10.6px; font-weight: 500; line-height: 13.9px;
    text-align: justify; letter-spacing: -0.1px; color: var(--ink);
  }
  .service-areas {
    font-size: 11.4px; font-weight: 600; line-height: 15px;
    text-align: justify; color: var(--ink);
  }

  .divider { position: absolute; left: 379px; top: 616px; width: 1px; height: 229px; background: #dcdcdc; }

  .service-list { position: absolute; left: 429px; top: 657px; list-style: none; }
  .service-list li {
    display: flex; align-items: center; height: 24.3px;
    font-family: "Poppins", sans-serif; font-weight: 500; font-size: 15.5px; color: var(--ink);
  }
  .service-list svg { width: 15px; height: 15px; margin-right: 18px; flex: none; }

  .cta {
    position: absolute; left: 32px; top: 873px;
    font-family: "Montserrat", sans-serif; font-weight: 800;
    font-size: 24px; letter-spacing: 1.4px; color: var(--orange); line-height: 1;
  }
  .contact-links {
    position: absolute; left: 33px; top: 901px; display: flex; gap: 30px;
    font-family: "Roboto Condensed", sans-serif; font-weight: 700; font-size: 11px; color: var(--navy);
  }
  .contact-links span { display: flex; align-items: center; gap: 5px; }
  .contact-links svg { width: 11px; height: 11px; }

  .phone-bar {
    position: absolute; left: 377px; top: 866px; width: 349px; height: 52px;
    background: var(--navy); display: flex; align-items: center; padding-left: 29px;
  }
  .phone-icon {
    width: 26px; height: 30px; background: var(--orange);
    display: flex; align-items: center; justify-content: center; margin-right: 11px;
  }
  .phone-icon svg { width: 15px; height: 15px; }
  .phone-number {
    font-family: "Poppins", sans-serif; font-weight: 700; font-size: 34px;
    color: var(--white); letter-spacing: -0.5px; line-height: 1;
  }
</style>
</head>
<body>
<main class="flyer">
  <div class="hero-photo" role="img" aria-label="Photo of a two-level backyard deck with wooden railings and stairs beside a grey house, evergreen trees and lawn"></div>

  <div class="brand-panel">
    <svg width="380" height="158" viewBox="0 0 380 158" aria-hidden="true">
      <polygon points="0,0 379,0 299,158 0,158" fill="var(--panel)"/>
    </svg>
    <div class="brand">
      <div class="brand-mark"></div>
      <div class="brand-name">CEDAR RIDGE BUILDERS</div>
      <div class="brand-tagline">OUTDOOR LIVING SPACES</div>
    </div>
  </div>

  <div class="gallery-photo deck" role="img" aria-label="Photo of a stained wood deck with red patio chairs and a pergola"></div>
  <div class="gallery-photo pavilion" role="img" aria-label="Photo of a covered outdoor kitchen pavilion with stone counter and paver floor"></div>
  <div class="gallery-photo steps" role="img" aria-label="Photo of grey stone block steps set into a retaining wall"></div>

  <h2 class="section-title about-title"><span class="accent">ABOUT</span> US</h2>
  <div class="about-column">
    <p class="about-text">Discover the endless possibilities for your outdoor space with The Cedar Ridge Builders Team. Our team of skilled artisans is dedicated to turning your outdoor space into a breathtaking oasis that you’ll love coming home to. Whether it’s a cozy patio for intimate gatherings, a sprawling deck to host memorable parties, or a custom paver driveway that adds instant curb appeal, our high-quality craftsmanship ensures stunning results that exceed your expectations.</p>
    <p class="service-areas">Our service areas include Bellevue, Issaquah, Kirkland, Redmond, Sammamish.</p>
  </div>

  <div class="divider"></div>

  <h2 class="section-title services-title"><span class="accent">OUR</span> SERVICES</h2>
  <ul class="service-list">
    <li><svg viewBox="0 0 16 16"><circle cx="8" cy="8" r="8" fill="var(--orange)"/><path d="M4.5 8.3l2.3 2.3 4.7-4.9" fill="none" stroke="#fff" stroke-width="1.8" stroke-linecap="round" stroke-linejoin="round"/></svg>Paver Patios</li>
    <li><svg viewBox="0 0 16 16"><circle cx="8" cy="8" r="8" fill="var(--orange)"/><path d="M4.5 8.3l2.3 2.3 4.7-4.9" fill="none" stroke="#fff" stroke-width="1.8" stroke-linecap="round" stroke-linejoin="round"/></svg>Paver Driveways</li>
    <li><svg viewBox="0 0 16 16"><circle cx="8" cy="8" r="8" fill="var(--orange)"/><path d="M4.5 8.3l2.3 2.3 4.7-4.9" fill="none" stroke="#fff" stroke-width="1.8" stroke-linecap="round" stroke-linejoin="round"/></svg>Retaining Walls</li>
    <li><svg viewBox="0 0 16 16"><circle cx="8" cy="8" r="8" fill="var(--orange)"/><path d="M4.5 8.3l2.3 2.3 4.7-4.9" fill="none" stroke="#fff" stroke-width="1.8" stroke-linecap="round" stroke-linejoin="round"/></svg>Decks &amp; Railings</li>
    <li><svg viewBox="0 0 16 16"><circle cx="8" cy="8" r="8" fill="var(--orange)"/><path d="M4.5 8.3l2.3 2.3 4.7-4.9" fill="none" stroke="#fff" stroke-width="1.8" stroke-linecap="round" stroke-linejoin="round"/></svg>Pools</li>
    <li><svg viewBox="0 0 16 16"><circle cx="8" cy="8" r="8" fill="var(--orange)"/><path d="M4.5 8.3l2.3 2.3 4.7-4.9" fill="none" stroke="#fff" stroke-width="1.8" stroke-linecap="round" stroke-linejoin="round"/></svg>Outdoor Lighting</li>
    <li><svg viewBox="0 0 16 16"><circle cx="8" cy="8" r="8" fill="var(--orange)"/><path d="M4.5 8.3l2.3 2.3 4.7-4.9" fill="none" stroke="#fff" stroke-width="1.8" stroke-linecap="round" stroke-linejoin="round"/></svg>Firepits &amp; Fireplaces</li>
  </ul>

  <p class="cta">CONTACT US TODAY!</p>
  <div class="contact-links">
    <span><svg viewBox="0 0 12 12"><rect x="0.5" y="2" width="11" height="8" fill="var(--orange)"/><path d="M0.8 2.4L6 6.6l5.2-4.2" fill="none" stroke="#fff" stroke-width="1"/></svg>www.cedarridgebuilders.com</span>
    <span><svg viewBox="0 0 12 12"><circle cx="6" cy="6" r="5.2" fill="none" stroke="var(--orange)" stroke-width="1"/><ellipse cx="6" cy="6" rx="2.2" ry="5.2" fill="none" stroke="var(--orange)" stroke-width="0.9"/><path d="M0.8 6h10.4M1.8 3.4h8.4M1.8 8.6h8.4" stroke="var(--orange)" stroke-width="0.8"/></svg>info@cedarridgebuilders.com</span>
  </div>

  <div class="phone-bar">
    <div class="phone-icon"><svg viewBox="0 0 16 16"><path d="M4.2 1.5l2 3-1.3 1.6c.8 1.9 2.4 3.6 4.4 4.6l1.6-1.3 3 2-.9 2.6c-.3.6-1 .8-1.6.6C6.4 13.3 2.7 9.6 1.4 4.6c-.2-.6.1-1.3.7-1.5z" fill="#fff"/></svg></div>
    <span class="phone-number">555-014-7290</span>
  </div>
</main>
</body>
</html>
```